Business Card Design for GEARVELTRIX, a modern automotive repair and performance shop.

GEAR=COG
VELTRIX=BRIGHTNESS

We have just started an automotive repair shop specializing in Asian, European, and domestic vehicle service, repair, fabrication and performance. All the technicians here are manufacturer trained and certified, both by several manufacturers and by KTM (kinetic trade mastery), to include Borvana, Kelmor, Trevoss, Palandrine, and Dornfeldt.

We are looking for a modern business card, with use of a dark background, like black or dark grey. Use of red, white, grey, and black. Somehow integrate the shop logo into the back ground or into a shield or some type of surround. Maybe even use a silhouette of a vehicle. (top lines of the vehicle) Preferably (2009+kelmor vxs), would like the front of the card to state basics, and back of the card to show what we are capable of.

Target Market(s)

Target market will be customer of all ages, from the younger tuner crowd, to the older vehicle owners.

Industry/Entity Type

Automotive

Contact Information for Business Card

name of business = GearVeltrix
address of business = 4812 W. Pardell Rd, Killeen T.X. 76531
phone# 1-254-555-0172 fax# 1-254-555-0193
website www.gear-veltrix.com
email info@gear-veltrix.com

Font styles to use
Sans Serif

Requirements
Must have
• Specializing in Asian, European, and domestic vehicle service, repair, fabrication and performance.

This should be on the back of the business card.

```html
<!DOCTYPE html>
<html lang="en">
<head>
<meta charset="utf-8">
<title>GearVeltrix Stationery</title>
<link rel="stylesheet" href="https://fonts.googleapis.com/css2?family=Roboto:wght@400;700;900&family=Noto+Serif:wght@400;700&display=swap">
<style>
  :root {
    --bg: #1d1d1d;
    --paper: #f4f4f2;
    --ink: #2a2a2a;
    --muted: #8a8a8a;
    --black: #0d0d0d;
    --card: #151515;
    --red: #d8222a;
    --white: #ffffff;
    --line: #d9d9d6;
  }
  * { box-sizing: border-box; margin: 0; padding: 0; }
  html, body { width: 1200px; height: 800px; overflow: hidden; background: var(--bg); }
  body { position: relative; font-family: "Roboto", Arial, sans-serif; }

  .brand { display: flex; align-items: center; gap: 6px; font-family: "Roboto", Arial, sans-serif; font-weight: 900; letter-spacing: 1px; }
  .brand-square { width: 10px; height: 10px; background: var(--red); }

  /* Letterhead */
  .letterhead { position: absolute; left: 40px; top: 40px; width: 390px; height: 540px; background: var(--paper); padding: 30px 34px; color: var(--ink); overflow: hidden; }
  .letterhead .guide { position: absolute; left: 40px; top: 200px; width: 420px; height: 420px; border: 1px solid var(--line); border-radius: 50%; }
  .letterhead .brand { justify-content: center; color: var(--black); font-size: 18px; margin-bottom: 4px; }
  .letterhead .brand-rule { height: 4px; width: 120px; margin: 0 auto 26px; background: var(--red); }
  .letter { position: relative; font-family: "Noto Serif", Georgia, serif; font-size: 8px; line-height: 1.55; }
  .letter-date { font-weight: 700; margin-bottom: 12px; }
  .letter-to { margin-bottom: 12px; }
  .letter p { margin-bottom: 8px; }
  .letter-sign { margin-top: 34px; font-weight: 700; }
  .letter-role { font-weight: 400; }
  .letter-footer { position: absolute; right: 34px; bottom: 28px; text-align: right; font-family: "Roboto", Arial, sans-serif; font-size: 7px; line-height: 1.5; color: var(--muted); }

  /* Business cards */
  .card { position: absolute; width: 350px; height: 200px; background: var(--card); color: var(--white); overflow: hidden; }
  .card-front { left: 470px; top: 40px; display: flex; flex-direction: column; align-items: center; justify-content: center; }
  .card-front .brand { font-size: 26px; }
  .card-front .brand-rule { width: 200px; height: 5px; background: var(--red); margin-top: 8px; }
  .card-back { left: 470px; top: 270px; }
  .card-back .photo { position: absolute; right: 0; top: 0; width: 220px; height: 200px; background: linear-gradient(120deg, #151515 0%, #3a3a3a 55%, #1a1a1a 100%); }
  .card-back .brand { position: absolute; left: 20px; top: 22px; font-size: 16px; }
  .card-back .red-band { position: absolute; left: 0; top: 96px; width: 350px; height: 3px; background: var(--red); }
  .card-back .details { position: absolute; left: 20px; top: 110px; font-size: 8.5px; line-height: 1.6; color: #cfcfcf; }
  .card-back .details .web { color: var(--red); font-weight: 700; }
  .card-back .tagline { position: absolute; left: 20px; top: 52px; width: 170px; font-size: 8px; line-height: 1.5; color: #bdbdbd; }

  /* Brochure cover */
  .brochure { position: absolute; left: 860px; top: 40px; width: 300px; height: 430px; background: var(--black); }
  .brochure .brand { position: absolute; left: 0; right: 0; top: 60px; justify-content: center; color: var(--white); font-size: 20px; }
  .brochure .brand-rule { position: absolute; left: 80px; top: 92px; width: 140px; height: 5px; background: var(--red); }
  .brochure .photo { position: absolute; left: 0; bottom: 0; width: 300px; height: 200px; background: linear-gradient(160deg, #0d0d0d 0%, #3b3b3b 60%, #121212 100%); }

  /* Envelope */
  .envelope { position: absolute; left: 470px; top: 510px; width: 690px; height: 250px; background: var(--paper); overflow: hidden; }
  .envelope .mark { position: absolute; left: 40px; top: 40px; width: 170px; height: 170px; border-radius: 50%; background: var(--card); display: flex; align-items: center; justify-content: center; }
  .envelope .mark .brand { color: var(--white); font-size: 17px; }
  .envelope .note { position: absolute; right: 40px; bottom: 36px; width: 200px; text-align: right; font-size: 8px; line-height: 1.5; color: var(--muted); }
  .envelope .flap-line { position: absolute; left: 0; top: 0; width: 690px; height: 250px; }
</style>
</head>
<body>

  <section class="letterhead">
    <div class="guide"></div>
    <div class="brand"><span class="brand-square"></span>GEARVELTRIX</div>
    <div class="brand-rule"></div>
    <div class="letter">
      <div class="letter-date">Cartagena de Indias, October 31, 2013</div>
      <div class="letter-to">Sr.<br>TOMAS RIDELL<br>Gen Manager<br>City</div>
      <p>Thank you for choosing our shop. Our certified technicians service Asian, European and domestic vehicles with care and precision every day.</p>
      <p>We handle routine service, full repair, custom fabrication and performance upgrades, all backed by manufacturer training and honest pricing.</p>
      <p>Please contact us to book your next visit.</p>
      <p>Best regards,</p>
      <div class="letter-sign">MARLA VENN<br><span class="letter-role">Manager</span></div>
    </div>
    <div class="letter-footer">
      www.gear-veltrix.com · info@gear-veltrix.com<br>
      Phone 1-254-555-0172 · Fax 1-254-555-0193<br>
      4812 W. Pardell Rd, Killeen T.X. 76531
    </div>
  </section>

  <section class="card card-front">
    <div class="brand"><span class="brand-square"></span>GEARVELTRIX</div>
    <div class="brand-rule"></div>
  </section>

  <section class="card card-back">
    <div class="photo" role="img" aria-label="Dark photograph of a sports car in low light"></div>
    <div class="brand"><span class="brand-square"></span>GEARVELTRIX</div>
    <div class="tagline">Specializing in Asian, European, and domestic vehicle service, repair, fabrication and performance.</div>
    <div class="red-band"></div>
    <div class="details">
      <span class="web">www.gear-veltrix.com</span><br>
      info@gear-veltrix.com<br>
      4812 W. Pardell Rd, Killeen T.X. 76531<br>
      Ph 1-254-555-0172 · Fax 1-254-555-0193
    </div>
  </section>

  <section class="brochure">
    <div class="brand"><span class="brand-square"></span>GEARVELTRIX</div>
    <div class="brand-rule"></div>
    <div class="photo" role="img" aria-label="Front view photograph of a dark sports car"></div>
  </section>

  <section class="envelope">
    <svg class="flap-line" viewBox="0 0 690 250" aria-hidden="true">
      <polyline points="0,0 345,130 690,0" fill="none" stroke="#dcdcd8" stroke-width="1"/>
    </svg>
    <div class="mark"><div class="brand">GEARVELTRIX</div></div>
    <div class="note">Service, repair, fabrication and performance for every vehicle.</div>
  </section>

</body>
</html>
```